Business cards to launch an education platform

Hi,
I am looking at having new business cards designed.
I am a startup, developing a web platform for schools and university, the education world. It's an online assessment system.
I would like a card that looks classy, and that is using the colors and the font of my logo.

I have attached:
1) my logo
2) A business card that I have designed quickly so you can have all the information required in the card, but I really don't like it.
3) The font that I am using (Lato Regular) to design my web platform
4) Some screenshots of my web platform so you can have a look at the style that I have.

Target Market(s)

Major market: Education system: Schools and university
Minor markets: Business in general

Industry/Entity Type

Business

Contact Information for Business Card

Clara Fenwick
Director

M: 0437 518 902
E: clara.fenwick@amberLoomSystems.com.au

Requirements
Must have
• The colors of my logo

```html
<!DOCTYPE html>
<html lang="en">
<head>
<meta charset="utf-8">
<title>Amber Loom Systems – Business Card</title>
<link rel="stylesheet" href="https://fonts.googleapis.com/css2?family=Lato:wght@400;700&display=swap">
<style>
  :root {
    --page-bg: #e6e8eb;
    --brand-blue: #1172c9;
    --brand-blue-light: #2b9ae6;
    --brand-blue-deep: #0a5ead;
    --navy: #17376b;
    --ink: #1d1d1f;
    --card-white: #ffffff;
  }
  * { margin: 0; padding: 0; box-sizing: border-box; }
  html, body {
    width: 1200px; height: 864px; overflow: hidden;
    background: var(--page-bg);
    font-family: "Lato", Arial, sans-serif;
  }
  .stage {
    width: 1200px; height: 864px;
    display: flex; flex-direction: column;
    align-items: center; justify-content: center; gap: 48px;
  }
  .card {
    width: 560px; height: 320px; position: relative;
    border-radius: 4px; overflow: hidden;
    box-shadow: 0 6px 18px rgba(0,0,0,0.18);
  }
  /* Front */
  .card-front {
    background: radial-gradient(ellipse at 50% 40%, var(--brand-blue-light) 0%, var(--brand-blue) 45%, var(--brand-blue-deep) 100%);
    display: flex; flex-direction: column; align-items: center; justify-content: center;
    color: var(--card-white);
  }
  .front-wordmark { font-size: 40px; font-weight: 400; letter-spacing: 4px; line-height: 1; }
  .front-tagline { font-size: 30px; font-weight: 400; letter-spacing: 3px; margin-top: 6px; line-height: 1; }
  /* Back */
  .card-back { background: var(--card-white); }
  .brand-lockup {
    position: absolute; top: 40px; right: 36px;
    display: flex; align-items: center; gap: 12px;
  }
  .brand-square { width: 58px; height: 58px; background: var(--brand-blue); border-radius: 3px; }
  .brand-name { color: var(--navy); font-weight: 400; line-height: 1.05; }
  .brand-name .line-one { display: block; font-size: 27px; letter-spacing: 3px; }
  .brand-name .line-two { display: block; font-size: 20px; letter-spacing: 2.5px; }
  .holder { position: absolute; left: 36px; top: 138px; }
  .holder-name { color: var(--brand-blue); font-size: 21px; font-weight: 400; line-height: 1.1; }
  .holder-role { color: var(--ink); font-size: 13px; line-height: 1.2; }
  .contact {
    position: absolute; right: 30px; bottom: 34px;
    display: flex; flex-direction: column; align-items: flex-end; gap: 8px;
    color: var(--ink);
  }
  .contact-row { display: flex; align-items: center; gap: 8px; font-size: 15px; letter-spacing: 0.3px; }
  .contact-icon { width: 12px; height: 12px; fill: var(--brand-blue); }
</style>
</head>
<body>
  <main class="stage">
    <section class="card card-front" aria-label="Card front">
      <div class="front-wordmark">AMBER</div>
      <div class="front-tagline">Loom Systems</div>
    </section>

    <section class="card card-back" aria-label="Card back">
      <div class="brand-lockup">
        <span class="brand-square"></span>
        <span class="brand-name">
          <span class="line-one">AMBER</span>
          <span class="line-two">Loom Systems</span>
        </span>
      </div>

      <div class="holder">
        <div class="holder-name">Clara Fenwick</div>
        <div class="holder-role">Director</div>
      </div>

      <div class="contact">
        <div class="contact-row">
          <span>0437 518 902</span>
          <svg class="contact-icon" viewBox="0 0 24 24" aria-hidden="true"><path d="M6.6 10.8a15.1 15.1 0 0 0 6.6 6.6l2.2-2.2c.3-.3.7-.4 1-.2 1.1.4 2.3.6 3.6.6.6 0 1 .4 1 1V20c0 .6-.4 1-1 1A17 17 0 0 1 3 4c0-.6.4-1 1-1h3.5c.6 0 1 .4 1 1 0 1.3.2 2.5.6 3.6.1.3 0 .7-.2 1z"/></svg>
        </div>
        <div class="contact-row">
          <span>clara.fenwick@amberLoomSystems.com.au</span>
          <svg class="contact-icon" viewBox="0 0 24 24" aria-hidden="true"><path d="M2 5h20v14H2z M3 6l9 7 9-7" fill="var(--brand-blue)" stroke="#fff" stroke-width="1.5"/></svg>
        </div>
      </div>
    </section>
  </main>
</body>
</html>
```